BrindleStaffing Business Card Design

We are a staffing company finding positions for dedicated nurses and physicians.

Target Market(s)

Business Professionals

Industry/Entity Type

Staffing

Contact Information for Business Card

Gordon Pratley
Chairman
417 39th Avenue South
SAINT PETERSBURG FL 33712
813-555-4172 Mobile
813-555-8036 Fax
gpratley@brindlestaffing.com
www.brindlestaffing.com

Font styles to use
Sans Serif

Colors
fbee3e
f04a50
f37122

Requirements
Must have
• Logo Attached, see colors below. We'd like to see Yellow, Orange and Red.

```html
<!DOCTYPE html>
<html lang="en">
<head>
<meta charset="utf-8">
<title>BrindleStaffing Business Card</title>
<link href="https://fonts.googleapis.com/css2?family=Poppins:wght@400;600;700&family=Source+Sans+3:wght@400;700&display=swap" rel="stylesheet">
<style>
  :root {
    --yellow: #fbee3e;
    --orange: #f37122;
    --red: #f04a50;
    --white: #ffffff;
    --stage-light: #8f9093;
    --stage-dark: #454448;
  }
  * { margin: 0; padding: 0; box-sizing: border-box; }
  html, body { width: 1200px; height: 1135px; overflow: hidden; }
  body {
    position: relative;
    background: radial-gradient(ellipse 60% 60% at 50% 48%, var(--stage-light), var(--stage-dark));
    font-family: "Source Sans 3", sans-serif;
  }
  .card {
    position: absolute;
    width: 711px;
    height: 406px;
    border-radius: 36px;
    overflow: hidden;
  }
  .card-front { left: 97px; top: 105px; background: var(--white); }
  .card-back { left: 397px; top: 590px; background: var(--orange); }
  .front-waves { position: absolute; inset: 0; }
  .brand-name {
    position: absolute;
    left: 0; right: 0;
    text-align: center;
    font-family: "Poppins", sans-serif;
    font-weight: 600;
    letter-spacing: -1px;
    line-height: 1;
  }
  .card-front .brand-name { top: 64px; font-size: 50px; color: var(--orange); left: -10px; }
  .card-back .brand-name { top: 148px; font-size: 56px; color: var(--white); }
  .holder {
    position: absolute;
    left: -20px; right: 0; top: 176px;
    text-align: center;
    font-family: "Poppins", sans-serif;
    font-size: 28px;
    line-height: 1.2;
  }
  .holder-name { color: var(--orange); font-weight: 700; }
  .holder-title { color: var(--red); font-weight: 400; }
  .contact {
    position: absolute;
    left: 0; right: 0;
    color: var(--white);
    font-size: 19px;
    text-align: center;
    line-height: 1;
    display: flex;
    justify-content: center;
    align-items: center;
    gap: 7px;
  }
  .contact svg { width: 15px; height: 15px; flex: none; }
  .contact-phone { top: 294px; left: 3px; }
  .contact-online { top: 323px; left: -10px; }
  .contact-online .gap { width: 4px; }
  .contact-address { top: 362px; left: -10px; }
  .back-url {
    position: absolute;
    left: 0; right: 0; top: 255px;
    text-align: center;
    color: var(--white);
    font-size: 21px;
    letter-spacing: 2.5px;
  }
  .back-url strong { font-weight: 700; color: var(--yellow); }
</style>
</head>
<body>
  <section class="card card-front">
    <svg class="front-waves" viewBox="0 0 711 406" aria-hidden="true">
      <path d="M0,326 Q355,166 711,326" fill="none" stroke="var(--red)" stroke-width="4"/>
      <path d="M0,330 Q355,192 711,330 L711,406 L0,406 Z" fill="var(--orange)"/>
    </svg>
    <div class="brand-name">BrindleStaffing</div>
    <div class="holder"><span class="holder-name">Gordon Pratley,</span> <span class="holder-title">Chairman</span></div>
    <div class="contact contact-phone">
      <svg viewBox="0 0 16 16"><circle cx="8" cy="8" r="7" fill="none" stroke="#fff" stroke-width="1.3"/><path d="M5.5 4.5c-.8.8-.5 2.6 1.2 4.6 1.8 2 3.6 2.6 4.4 1.8l-1.3-1.4-1 .5c-.8-.4-1.6-1.3-1.9-2.2l.6-.9z" fill="#fff"/></svg>
      <span>813-555-4172</span>
    </div>
    <div class="contact contact-online">
      <svg viewBox="0 0 16 16"><rect x="1" y="5" width="14" height="9" fill="#fff"/><path d="M1 5l7 5 7-5" fill="none" stroke="var(--orange)" stroke-width="1.3"/><path d="M3 5l5-3 5 3" fill="#fff"/></svg>
      <span>gpratley@brindlestaffing.com</span>
      <span class="gap"></span>
      <svg viewBox="0 0 16 16"><g fill="none" stroke="#fff" stroke-width="1.2"><circle cx="8" cy="8" r="6.5"/><ellipse cx="8" cy="8" rx="3" ry="6.5"/><path d="M1.5 8h13M2.5 4.8h11M2.5 11.2h11"/></g></svg>
      <span>www.brindlestaffing.com</span>
    </div>
    <div class="contact contact-address">417 39th Avenue South, Saint petersburg fl 33712</div>
  </section>

  <section class="card card-back">
    <div class="brand-name">BrindleStaffing</div>
    <div class="back-url">www.<strong>brindlestaffing</strong>.com</div>
  </section>
</body>
</html>
```